Brook Refrigeration. Refrigeration and air conditioning specialists.

We need a website to promote our business. We would a modern simple design using the colours from our logo and black. We want it to be fun but proffesional.

Target Market(s)

Commercial

Number of Pages Required

4 page

Requirements
Must have
• Home Page, About Us, Services and Contact Us.
• 24/7 365 days service available.
• Brook Refrigeration's dedicated team specialises in commercial refrigeration and air conditioning equipment.
• Based in Westvale, we cover Westvale Metro and surrounding areas.
Nice to have
• KNOWLEDGE . EXPERIENCE . PASSION in bold.
• Our experienced and highly trained technicians provide extensive knowledge and exceptional skills for your commercial refrigeration and air conditioning requirements.
• Pictures of commercial refrigeration.
Should not have
• No mention of domestic services.

```html
<!DOCTYPE html>
<html lang="en">
<head>
<meta charset="utf-8">
<title>Brook Refrigeration</title>
<link href="https://fonts.googleapis.com/css2?family=Montserrat:wght@600;700;800&family=Open+Sans:wght@400;600;700&display=swap" rel="stylesheet">
<style>
:root{
  --green:#8fd13f;
  --purple:#3a2266;
  --purple-deep:#2c1850;
  --ink:#1c1c1c;
  --muted:#8a8a8a;
  --white:#ffffff;
}
*{box-sizing:border-box;margin:0;padding:0}
html,body{width:1200px;height:2592px;overflow:hidden;background:var(--white)}
body{font-family:"Open Sans",Arial,sans-serif;color:var(--ink)}
.page{position:relative;width:1200px;height:2592px;overflow:hidden}
.abs{position:absolute}

/* top bar + header */
.topbar{left:830px;top:0;width:370px;height:30px;background:var(--green);color:var(--ink);font-size:14px;font-weight:600;display:flex;align-items:center;justify-content:center;gap:8px;white-space:nowrap}
.header{left:0;top:0;width:1200px;height:112px}
.brand{left:96px;top:40px;display:flex;align-items:center;gap:12px}
.brand-mark{width:26px;height:26px;background:var(--green)}
.brand-name{font-family:"Montserrat",sans-serif;font-weight:800;font-size:24px;color:var(--green);letter-spacing:.5px;white-space:nowrap}
.nav{left:455px;top:62px;display:flex;gap:42px;font-family:"Montserrat",sans-serif;font-weight:600;font-size:16px;color:var(--ink);white-space:nowrap}
.tools{left:960px;top:56px;display:flex;gap:12px;align-items:center}
.dot{width:26px;height:26px;border-radius:50%}

/* hero */
.hero{left:0;top:112px;width:1200px;height:658px;background:linear-gradient(180deg,#cfd6dc 0%,#e9ecef 45%,#f4f5f6 100%)}
.hero-band{left:152px;top:376px;width:896px;height:72px;background:var(--green);display:flex;align-items:center;justify-content:center;font-family:"Montserrat",sans-serif;font-weight:800;font-size:34px;letter-spacing:1.5px;color:var(--ink);white-space:nowrap}
.hero-band .hl{color:var(--white)}
.hero-dots{left:572px;top:656px;display:flex;gap:14px}
.hero-dots i{width:10px;height:10px;border-radius:50%;background:#c9c9c9;display:block}
.hero-dots i.on{background:#555}

/* about */
.label{font-family:"Montserrat",sans-serif;font-weight:700;font-size:16px;color:var(--ink);display:flex;align-items:center;gap:10px;letter-spacing:.5px;white-space:nowrap}
.label b{width:12px;height:4px;background:var(--green);display:block}
.about-label{left:100px;top:846px}
.about-title{left:254px;top:818px;font-family:"Montserrat",sans-serif;font-weight:800;font-size:54px;color:var(--purple)}
.about-title span{color:var(--green)}
.about-copy{left:254px;top:898px;width:780px;font-size:15px;line-height:27px;color:var(--muted)}
.btn-outline{left:254px;top:1050px;width:146px;height:44px;border:2px solid var(--green);border-radius:22px;display:flex;align-items:center;justify-content:center;font-family:"Montserrat",sans-serif;font-weight:700;font-size:14px;color:var(--ink)}

/* feature images */
.feature-left{left:0;top:1180px;width:610px;height:420px;background:linear-gradient(160deg,#d7dfe3 0%,#eef1f2 50%,#c8cfa8 100%);clip-path:polygon(0 0,100% 0,96% 100%,0 100%)}
.feature-right{left:570px;top:1168px;width:630px;height:424px;background:linear-gradient(180deg,#e6e8ea 0%,#8f9aa3 55%,#3f6d2b 100%);clip-path:polygon(4% 0,100% 0,100% 100%,0 100%)}
.tag{height:56px;display:flex;align-items:center;font-family:"Montserrat",sans-serif;font-weight:800;font-size:22px;letter-spacing:.5px;white-space:nowrap}
.tag-green{left:0;top:1364px;width:410px;background:var(--green);color:var(--ink);padding-left:16px}
.tag-purple{left:690px;top:1364px;width:510px;background:var(--purple);color:var(--green);padding-left:22px}

/* services */
.services-label{left:944px;top:1622px;flex-direction:row-reverse}
.service{top:1696px;width:300px;text-align:center}
.service .ring{width:84px;height:84px;margin:0 auto;border:3px solid var(--green);border-radius:50%;display:flex;align-items:center;justify-content:center}
.service h3{margin-top:30px;font-family:"Montserrat",sans-serif;font-weight:700;font-size:17px;color:var(--ink);white-space:nowrap}
.service p{margin-top:12px;font-size:13px;line-height:21px;color:var(--muted)}
.contact-label{left:968px;top:2020px;flex-direction:row-reverse}

/* contact */
.contact{left:0;top:2040px;width:1200px;height:552px;background:linear-gradient(180deg,var(--purple) 0%,var(--purple-deep) 100%);clip-path:polygon(0 70px,78% 30px,78% 0,100% 0,100% 100%,0 100%)}
.contact-title{left:0;top:2112px;width:1200px;text-align:center;font-family:"Montserrat",sans-serif;font-weight:800;font-size:50px;color:var(--white)}
.contact-title span{color:var(--green)}
.col-title{font-weight:700;font-size:16px;color:var(--white)}
.form{left:96px;top:2188px;width:610px}
.row{display:flex;gap:12px;margin-top:14px}
.field{height:32px;background:var(--white);font-size:12px;color:#888;padding:8px 10px;flex:1}
.field.tall{height:70px}
.submit{left:578px;top:2408px;width:124px;height:40px;border-radius:20px;background:var(--green);display:flex;align-items:center;justify-content:center;font-family:"Montserrat",sans-serif;font-weight:700;font-size:14px;color:var(--ink)}
.info{left:780px;top:2188px;width:340px}
.info-row{display:flex;align-items:center;gap:16px;margin-top:20px;font-size:13px;line-height:19px;color:#d8d0e8}
.info-icon{width:36px;height:36px;border-radius:50%;background:var(--white);flex:none;display:flex;align-items:center;justify-content:center}
.info-social{display:flex;gap:8px;margin-top:20px}
.info-social i{width:24px;height:24px;border-radius:50%;display:block}
.rule{left:96px;top:2536px;width:1008px;height:1px;background:rgba(255,255,255,.2)}
.copyright{left:0;top:2552px;width:1200px;text-align:center;font-size:12px;color:#cfc6e0}
</style>
</head>
<body>
<div class="page">

  <header class="abs header">
    <div class="abs topbar">
      <svg width="14" height="14" viewBox="0 0 24 24"><path d="M6.6 10.8a15 15 0 0 0 6.6 6.6l2.2-2.2c.3-.3.7-.4 1-.2 1.1.4 2.3.6 3.6.6.6 0 1 .4 1 1V20c0 .6-.4 1-1 1A17 17 0 0 1 3 4c0-.6.4-1 1-1h3.5c.6 0 1 .4 1 1 0 1.3.2 2.5.6 3.6.1.3 0 .7-.2 1z" fill="#1c1c1c"/></svg>
      24/7 365 days Service Available
    </div>
    <div class="abs brand"><span class="brand-mark"></span><span class="brand-name">Brook Refrigeration</span></div>
    <nav class="abs nav"><span>Home</span><span>About Us</span><span>Services</span><span>Contact Us</span></nav>
    <div class="abs tools">
      <svg width="20" height="20" viewBox="0 0 24 24"><circle cx="10" cy="10" r="6.5" fill="none" stroke="#1c1c1c" stroke-width="2.4"/><path d="M15 15l6 6" stroke="#1c1c1c" stroke-width="2.6" stroke-linecap="round"/></svg>
      <span class="dot" style="background:#3b5998"></span>
      <span class="dot" style="background:#1da1f2"></span>
      <span class="dot" style="background:#d9232d"></span>
    </div>
  </header>

  <section class="abs hero" role="img" aria-label="Photo of a commercial cool room with display fridges and shelving"></section>
  <svg class="abs" style="left:0;top:560px" width="1200" height="212" viewBox="0 0 1200 212"><polygon points="0,0 620,212 0,212" fill="#ffffff"/><rect x="0" y="210" width="1200" height="2" fill="#ffffff"/></svg>
  <div class="abs hero-band">KNOWLEDGE&nbsp;.&nbsp;<span class="hl">EXPERIENCE</span>&nbsp;.&nbsp;PASSION</div>
  <div class="abs hero-dots"><i></i><i class="on"></i><i></i></div>

  <div class="abs label about-label"><b></b>ABOUT</div>
  <h1 class="abs about-title">ABOUT <span>US</span></h1>
  <p class="abs about-copy">Brook Refrigeration's dedicated team specialises in commercial refrigeration and air conditioning equipment. Our experienced and highly trained technicians provide extensive knowledge and exceptional skills for your commercial requirements. Based in Westvale, we cover Westvale Metro and surrounding areas, with service available 24/7, 365 days a year.</p>
  <div class="abs btn-outline">READ MORE</div>

  <div class="abs feature-left" role="img" aria-label="Photo of a commercial cool room with metal shelving"></div>
  <div class="abs feature-right" role="img" aria-label="Photo of outdoor air conditioning units on grass"></div>
  <div class="abs tag tag-green">COMMERCIAL REFRIGERATION</div>
  <div class="abs tag tag-purple">AIR CONDITIONING EQUIPMENT</div>

  <div class="abs label services-label"><b></b>OUR SERVICES</div>

  <div class="abs service" style="left:90px">
    <div class="ring"><svg width="38" height="38" viewBox="0 0 24 24"><path d="M2 10h4v11H2zM8 21V10l5-8c1.3 0 2.3 1 2 2.4L14 9h6a2 2 0 0 1 2 2.3l-1.4 7.8A2.4 2.4 0 0 1 18.2 21z" fill="#3a2266"/></svg></div>
    <h3>HIGH QUALITY</h3>
    <p>Quality workmanship on every commercial job we take on.</p>
  </div>
  <div class="abs service" style="left:450px">
    <div class="ring"><svg width="38" height="38" viewBox="0 0 24 24"><path d="M21 6.5a5 5 0 0 1-6.6 4.8L5.6 20a2 2 0 0 1-2.8-2.8l8.7-8.8A5 5 0 0 1 17.5 2l-3 3 .5 3.5 3.5.5z" fill="#3a2266"/></svg></div>
    <h3>NEMO ENIM IPSA</h3>
    <p>Fast response from technicians who know your equipment.</p>
  </div>
  <div class="abs service" style="left:810px">
    <div class="ring"><svg width="36" height="36" viewBox="0 0 24 24"><rect x="4" y="2" width="16" height="20" rx="1.5" fill="none" stroke="#3a2266" stroke-width="2"/><path d="M8 7h8M8 11h8M8 15h8M8 19h5" stroke="#3a2266" stroke-width="2"/></svg></div>
    <h3>CONSEQUUNTUR</h3>
    <p>Clear reports and honest advice after every service call.</p>
  </div>

  <div class="abs label contact-label"><b></b>CONTACT US</div>

  <section class="abs contact"></section>
  <h2 class="abs contact-title">CONTACT <span>US</span></h2>

  <div class="abs form">
    <div class="col-title">Get In Touch:</div>
    <div class="row"><div class="field">Name</div><div class="field">Phone</div></div>
    <div class="row"><div class="field" style="flex:0 0 299px">Email</div><div style="flex:1"></div></div>
    <div class="row"><div class="field tall">Message</div></div>
  </div>
  <div class="abs submit">SUBMIT</div>

  <div class="abs info">
    <div class="col-title">Contact Info</div>
    <div class="info-row"><span class="info-icon"><svg width="16" height="16" viewBox="0 0 24 24"><path d="M12 2a7 7 0 0 0-7 7c0 5 7 13 7 13s7-8 7-13a7 7 0 0 0-7-7zm0 9.5A2.5 2.5 0 1 1 12 6.5a2.5 2.5 0 0 1 0 5z" fill="#3a2266"/></svg></span>Unit 4, 12 Harbour Lane, Westvale</div>
    <div class="info-row"><span class="info-icon"><svg width="15" height="15" viewBox="0 0 24 24"><path d="M6.6 10.8a15 15 0 0 0 6.6 6.6l2.2-2.2c.3-.3.7-.4 1-.2 1.1.4 2.3.6 3.6.6.6 0 1 .4 1 1V20c0 .6-.4 1-1 1A17 17 0 0 1 3 4c0-.6.4-1 1-1h3.5c.6 0 1 .4 1 1 0 1.3.2 2.5.6 3.6.1.3 0 .7-.2 1z" fill="#3a2266"/></svg></span>Phone : 1 800 555 012</div>
    <div class="info-row"><span class="info-icon"><svg width="16" height="16" viewBox="0 0 24 24"><rect x="3" y="5" width="18" height="14" rx="1.5" fill="#3a2266"/><path d="M3.5 6l8.5 7 8.5-7" fill="none" stroke="#fff" stroke-width="1.6"/></svg></span>Email: hello@brookrefrigeration.example</div>
    <div class="info-social"><i style="background:#3b5998"></i><i style="background:#1da1f2"></i><i style="background:#0e76a8"></i><i style="background:#d9232d"></i></div>
  </div>

  <div class="abs rule"></div>
  <p class="abs copyright">Copyright © 2024 Brook Refrigeration. All Rights Reserved. &nbsp;|&nbsp; Privacy policy &nbsp;|&nbsp; Terms and conditions</p>

</div>
</body>
</html>
```